Business Card for Multi-Brand Sportswear Company

We are looking for a business card which represents our company and the multiple brands within it.

The company: Fen Athletics (LTD)
The brands: Fen, TavaPuni, ElmStretch, Grit and Rain

Employees using these cards would be representing Fen Athletics, rather than any of the individual brands. You will see a current design within the uploaded files, to give some inspiration. The actual text of the brands is not necessary, but the logos should be on there is some format.

Our creative minds on this are stretched, so we are looking for someone to make this their own, and show us what a good business card should look like.

We may like to get these printed with spot gloss, so keep that in mind with your designs.

www.fenathletics.co.uk

Industry/Entity Type

Business

Contact Information for Business Card

Leo Pemberton-Hale
Operations Manager
(+44) 1632 960 418
Leo@fenathletics.co.uk
www.fenathletics.co.uk

Font styles to use
Sans Serif
Other font styles liked:
• Eurostile

Colors
ffffff

Requirements
Nice to have
• Dark (black) background

```html
<!DOCTYPE html>
<html lang="en">
<head>
<meta charset="utf-8">
<title>Fen Athletics – Business Card</title>
<link href="https://fonts.googleapis.com/css2?family=Exo+2:wght@400;500;700&display=swap" rel="stylesheet">
<style>
  :root {
    --backdrop: #2b2725;
    --card: #1b1c1f;
    --card-edge: #111214;
    --white: #ffffff;
    --text-soft: #d9d9dc;
    --red: #e3202c;
    --silver: #c9c9cc;
    --divider: #4a4b50;
    --mark-grey: #8d8e93;
    --mark-purple: #6b5a86;
  }
  * { margin: 0; padding: 0; box-sizing: border-box; }
  html, body {
    width: 1200px; height: 769px; overflow: hidden;
    background: var(--backdrop);
    font-family: "Exo 2", Arial, sans-serif;
  }
  .canvas {
    position: relative; width: 1200px; height: 769px;
    display: flex; align-items: center; justify-content: center; gap: 40px;
  }
  .card {
    position: relative; width: 540px; height: 349px;
    background: var(--card);
    border-radius: 4px;
    overflow: hidden;
    box-shadow: 0 10px 30px rgba(0,0,0,.45);
  }

  /* Front */
  .front .brand {
    position: absolute; left: 44px; top: 140px;
    color: var(--white); font-weight: 700; font-size: 30px; letter-spacing: .5px;
  }
  .front .divider {
    position: absolute; left: 272px; top: 70px; width: 1px; height: 180px;
    background: var(--divider);
  }
  .contact {
    position: absolute; left: 296px; top: 72px; color: var(--text-soft);
    font-size: 14px; line-height: 1.35;
  }
  .contact .name { color: var(--red); font-size: 20px; font-weight: 500; }
  .contact .role { margin-bottom: 12px; }
  .contact .address { margin-bottom: 12px; }
  .contact .line { display: flex; align-items: center; gap: 8px; }
  .contact svg { width: 12px; height: 12px; fill: var(--red); flex: none; }
  .front .footer { position: absolute; left: 0; bottom: 0; width: 540px; height: 80px; }
  .front .url {
    position: absolute; right: 26px; bottom: 38px;
    color: var(--card-edge); font-size: 13px; letter-spacing: 3px; font-weight: 500;
  }

  /* Back */
  .back .brand {
    position: absolute; left: 0; right: 0; top: 110px; text-align: center;
    color: var(--silver); font-weight: 700; font-size: 44px; letter-spacing: 1px;
  }
  .brand-row {
    position: absolute; left: 30px; right: 30px; bottom: 40px;
    display: flex; justify-content: space-between; align-items: center;
    font-size: 13px; font-weight: 500;
  }
  .brand-mark { display: flex; align-items: center; gap: 6px; }
  .brand-mark.fen { color: var(--white); font-weight: 700; font-size: 18px; }
  .brand-mark.tava { color: var(--mark-grey); }
  .brand-mark.tava .dot { width: 12px; height: 12px; border: 1.5px solid var(--mark-grey); border-radius: 50%; }
  .brand-mark.elm { color: var(--mark-purple); }
  .brand-mark.elm .sq { width: 12px; height: 12px; background: var(--mark-purple); }
  .brand-mark.grit { color: var(--red); }
</style>
</head>
<body>
<main class="canvas">
  <section class="card front" aria-label="Card front">
    <div class="brand">Fen Athletics</div>
    <div class="divider"></div>
    <div class="contact">
      <div class="name">Leo Pemberton-Hale</div>
      <div class="role">Managing Director</div>
      <div class="address">Marsh Yard, Eastholme<br>Ashby, ZZ9 4QT</div>
      <div class="line">
        <svg viewBox="0 0 24 24" aria-hidden="true"><path d="M6.6 10.8a15.2 15.2 0 0 0 6.6 6.6l2.2-2.2c.3-.3.7-.4 1-.2 1.1.4 2.3.6 3.6.6.6 0 1 .4 1 1V20c0 .6-.4 1-1 1A17 17 0 0 1 3 4c0-.6.4-1 1-1h3.5c.6 0 1 .4 1 1 0 1.3.2 2.5.6 3.6.1.3 0 .7-.2 1z"/></svg>
        +44 (0)1632 960418
      </div>
      <div class="line">
        <svg viewBox="0 0 24 24" aria-hidden="true"><path d="M2 5h20v14H2z M2 5l10 8 10-8" stroke="#1b1c1f" stroke-width="1.5"/></svg>
        leo@fenathletics.co.uk
      </div>
    </div>
    <svg class="footer" viewBox="0 0 540 80" aria-hidden="true">
      <polygon points="0,70 540,30 540,38 0,78" fill="#ffffff"/>
      <path d="M300 80 L300 52 Q300 36 318 34 L540 2 L540 80 Z" fill="#e3202c"/>
    </svg>
    <div class="url">www.fenathletics.co.uk</div>
  </section>

  <section class="card back" aria-label="Card back">
    <div class="brand">Fen Athletics</div>
    <div class="brand-row">
      <span class="brand-mark fen">Fen</span>
      <span class="brand-mark tava"><span class="dot"></span>TavaPuni</span>
      <span class="brand-mark elm"><span class="sq"></span>ElmStretch</span>
      <span class="brand-mark grit">Grit and Rain</span>
    </div>
  </section>
</main>
</body>
</html>
```